Heater product information sheets

I need the two product information sheets organized and laid out in a clean, easy to read attractive manner. These sheets are to advertise propane heaters for outdoor use and for wholesale to propane distributors, restaurants and homeowners that need to have propane heat as the winter ends and spring begins. They will be used for chilly evenings when people want to be outside eating, drinking and being social.

Target Market(s)

Restaurants, hospitality industry, special events, party rental companies, home owners with backyards

Font styles to use
Sans Serif

Requirements
Must have
• My logo in the document instead of t. Marlow and company
Nice to have
• I would like to see Fire illustrated coming up the heaters and on the round glass, show it up the middle of the glass tube propane heater.

```html
<!DOCTYPE html>
<html lang="en">
<head>
<meta charset="utf-8">
<title>Propane Heater Product Sheets</title>
<link rel="stylesheet" href="https://fonts.googleapis.com/css2?family=Roboto:wght@400;500;700;900&display=swap">
<style>
  :root {
    --orange: #f37a2d;
    --orange-soft: #f58a48;
    --ink: #141414;
    --white: #ffffff;
    --grey-text: #2a2a2a;
    --backdrop: #e4e4e2;
  }
  html, body {
    margin: 0;
    width: 1200px;
    height: 800px;
    overflow: hidden;
    background: var(--backdrop);
    font-family: "Roboto", Arial, sans-serif;
  }
  .canvas { position: relative; width: 1200px; height: 800px; }
  .sheet {
    position: absolute;
    top: 62px;
    width: 520px;
    height: 676px;
    box-shadow: 0 4px 14px rgba(0,0,0,0.25);
    background: var(--white);
  }
  .sheet--adjustable { left: 50px; }
  .sheet--spiral { left: 630px; }
  .sheet svg { display: block; width: 100%; height: 100%; }

  .title { font-weight: 900; font-size: 39px; fill: var(--white); }
  .title--accent { fill: var(--orange); }
  .perk { font-weight: 500; font-size: 11.5px; fill: var(--white); letter-spacing: 0.6px; }
  .section-head { font-weight: 900; font-size: 23px; fill: var(--ink); letter-spacing: 1.6px; }
  .spec { font-weight: 400; font-size: 12px; fill: var(--white); letter-spacing: 0.3px; }
  .detail { font-weight: 400; font-size: 12px; fill: var(--grey-text); }
  .bullet-dot { fill: var(--orange); }
  .spec-dot { fill: var(--white); }
  .note-head { font-weight: 900; font-size: 24px; fill: var(--white); letter-spacing: 1px; }
  .note-price { font-weight: 700; font-size: 15px; fill: var(--white); }
  .note-small { font-weight: 400; font-size: 8.5px; fill: var(--white); }
  .contact-head { font-weight: 700; font-size: 14px; fill: var(--orange); }
  .contact-name { font-weight: 700; font-size: 14px; fill: var(--white); }
  .contact-line { font-weight: 400; font-size: 12.5px; fill: var(--white); }
  .brand-name { font-weight: 900; font-size: 50px; fill: var(--ink); letter-spacing: -1px; }
  .brand-tagline { font-weight: 700; font-size: 10px; fill: var(--ink); }
</style>
</head>
<body>
<main class="canvas">

  <section class="sheet sheet--adjustable">
    <svg viewBox="0 0 612 795" xmlns="http://www.w3.org/2000/svg">
      <defs>
        <linearGradient id="patio-a" x1="0" y1="0" x2="1" y2="1">
          <stop offset="0" stop-color="#2f3d2a"/>
          <stop offset="0.55" stop-color="#1d241c"/>
          <stop offset="1" stop-color="#3a3a36"/>
        </linearGradient>
        <linearGradient id="product-a" x1="0" y1="0" x2="0" y2="1">
          <stop offset="0" stop-color="#b9b9b5"/>
          <stop offset="0.15" stop-color="#f3a23a"/>
          <stop offset="0.3" stop-color="#3a3a3a"/>
          <stop offset="1" stop-color="#141414"/>
        </linearGradient>
        <linearGradient id="paper-a" x1="0" y1="0" x2="1" y2="1">
          <stop offset="0" stop-color="#ffffff"/>
          <stop offset="0.6" stop-color="#f1f1f1"/>
          <stop offset="1" stop-color="#ffffff"/>
        </linearGradient>
      </defs>

      <rect class="patio-photo" x="0" y="0" width="612" height="340" fill="url(#patio-a)" role="img" aria-label="Photo of outdoor patio seating on a terrace with greenery"/>
      <path class="orange-wave" d="M0,250 C200,256 430,222 612,118 L612,795 L0,795 Z" fill="var(--orange)"/>
      <path class="paper-wave" d="M0,413 C210,405 440,330 612,232 L612,795 L0,795 Z" fill="url(#paper-a)"/>

      <text class="title" x="32" y="78">ADJUSTABLE</text>
      <text class="title" x="32" y="128">PROPANE</text>
      <text class="title title--accent" x="32" y="178">HEATER</text>
      <line x1="318" y1="42" x2="318" y2="195" stroke="#ffffff" stroke-opacity="0.55" stroke-width="1"/>

      <g class="perks">
        <circle cx="340" cy="64" r="6.5" fill="var(--orange)"/><path d="M337,64 l2.2,2.2 l4,-4.4" stroke="#fff" stroke-width="1.6" fill="none"/>
        <text class="perk" x="355" y="68">AVAILABLE TO PURCHASE</text>
        <circle cx="340" cy="93" r="6.5" fill="var(--orange)"/><path d="M337,93 l2.2,2.2 l4,-4.4" stroke="#fff" stroke-width="1.6" fill="none"/>
        <text class="perk" x="355" y="97">AVAILABLE TO RENT</text>
        <circle cx="340" cy="122" r="6.5" fill="var(--orange)"/><path d="M337,122 l2.2,2.2 l4,-4.4" stroke="#fff" stroke-width="1.6" fill="none"/>
        <text class="perk" x="355" y="126">SEASONAL RENTAL PROGRAMS</text>
        <text class="perk" x="355" y="140">FOR RESTAURANT AND HOSPITALITY</text>
        <text class="perk" x="355" y="155">COMPANIES</text>
      </g>

      <text class="section-head" x="33" y="292">SPECIFICATIONS</text>
      <g class="specs">
        <circle class="spec-dot" cx="37" cy="312" r="2"/><text class="spec" x="48" y="316">ADJUSTABLE UP TO 48,000 BTU</text>
        <circle class="spec-dot" cx="37" cy="331" r="2"/><text class="spec" x="48" y="335">BLACK POWDER COATED FINISH</text>
        <circle class="spec-dot" cx="37" cy="349" r="2"/><text class="spec" x="48" y="353">USES 20 LBS. PROPANE TANK</text>
        <circle class="spec-dot" cx="37" cy="368" r="2"/><text class="spec" x="48" y="372">CE, GS, AGA, CSA, WITH ETL CERTIFICATE</text>
        <text class="spec" x="48" y="391">AND ROHS APPROVED</text>
      </g>

      <rect class="product-photo" x="432" y="232" width="118" height="420" rx="36" fill="url(#product-a)" role="img" aria-label="Product photo of the adjustable propane patio heater with a flame in its glass burner"/>

      <text class="section-head" x="36" y="448">ADDITIONAL DETAILS</text>
      <g class="details">
        <circle class="bullet-dot" cx="37" cy="468" r="2"/><text class="detail" x="44" y="472">Commercial Quality</text>
        <circle class="bullet-dot" cx="37" cy="488" r="2"/><text class="detail" x="44" y="492">For Outdoor Use Only</text>
        <circle class="bullet-dot" cx="37" cy="508" r="2"/><text class="detail" x="44" y="512">Conforms to ANSI STD Z83.26-2014 Certified to CSA STD</text>
        <text class="detail" x="44" y="532">2.37-2014 Gas- fired outdoor infrared patio heaters</text>
        <circle class="bullet-dot" cx="37" cy="548" r="2"/><text class="detail" x="44" y="552">Safety Auto Shut Off Switch</text>
        <circle class="bullet-dot" cx="37" cy="568" r="2"/><text class="detail" x="44" y="572">Thermostatic Control</text>
        <circle class="bullet-dot" cx="37" cy="588" r="2"/><text class="detail" x="44" y="592">Piezoelectric ignition</text>
        <circle class="bullet-dot" cx="37" cy="608" r="2"/><text class="detail" x="44" y="612">Base Diameter 17” - Anti-Tip Design</text>
        <circle class="bullet-dot" cx="37" cy="628" r="2"/><text class="detail" x="44" y="632">Standard Wheels - Tilt &amp; Move</text>
        <circle class="bullet-dot" cx="37" cy="648" r="2"/><text class="detail" x="44" y="652">Run time: 8-10 hours with standard 20 lbs. Propane tank</text>
        <circle class="bullet-dot" cx="37" cy="668" r="2"/><text class="detail" x="44" y="672">88” Tall</text>
        <circle class="bullet-dot" cx="37" cy="688" r="2"/><text class="detail" x="44" y="692">Heating Area: 200 sq. ft</text>
      </g>

      <g class="price-note">
        <circle cx="526" cy="580" r="70" fill="var(--orange-soft)" fill-opacity="0.95"/>
        <text class="note-head" x="524" y="552" text-anchor="middle">NOTE</text>
        <text class="note-price" x="524" y="576" text-anchor="middle">$250 each</text>
        <text class="note-small" x="524" y="593" text-anchor="middle">Assembly &amp; Delivery available</text>
        <text class="note-small" x="524" y="604" text-anchor="middle">upon request. Discounts</text>
        <text class="note-small" x="524" y="615" text-anchor="middle">for large quantity orders</text>
      </g>

      <path class="footer-stripe" d="M185,795 C255,690 370,662 612,650 L612,795 Z" fill="var(--orange)"/>
      <path class="footer-band" d="M215,795 C280,700 380,676 612,664 L612,795 Z" fill="var(--ink)"/>

      <g class="contact">
        <text class="contact-head" x="595" y="706" text-anchor="end">FOR INQUIRIES AND ORDERS:</text>
        <text class="contact-name" x="595" y="723" text-anchor="end">Contact:  Dana Reyes</text>
        <text class="contact-line" x="572" y="744" text-anchor="end">555-014-2271</text>
        <text class="contact-line" x="572" y="762" text-anchor="end">dana@tmarlowco.example</text>
        <text class="contact-line" x="572" y="780" text-anchor="end">42 - 48 Harbor Lane Millbrook, NJ 07000</text>
        <circle cx="589" cy="740" r="6" fill="var(--orange)"/>
        <path d="M586.5,737.5 q0,4 5,5" stroke="#fff" stroke-width="1.5" fill="none"/>
        <circle cx="589" cy="758" r="6" fill="var(--orange)"/>
        <circle cx="589" cy="758" r="3" stroke="#fff" stroke-width="1.1" fill="none"/>
        <circle cx="589" cy="776" r="6" fill="var(--orange)"/>
        <path d="M589,779.5 l-2.6,-3.4 a2.8,2.8 0 1 1 5.2,0 Z" fill="#fff"/>
      </g>

      <g class="brand">
        <text class="brand-name" x="48" y="760">TMC</text>
        <text class="brand-tagline" x="36" y="775">t. Marlow and company</text>
      </g>
    </svg>
  </section>

  <section class="sheet sheet--spiral">
    <svg viewBox="0 0 612 795" xmlns="http://www.w3.org/2000/svg">
      <defs>
        <linearGradient id="patio-b" x1="0" y1="0" x2="1" y2="1">
          <stop offset="0" stop-color="#2f3d2a"/>
          <stop offset="0.55" stop-color="#1d241c"/>
          <stop offset="1" stop-color="#3a3a36"/>
        </linearGradient>
        <linearGradient id="product-b" x1="0" y1="0" x2="0" y2="1">
          <stop offset="0" stop-color="#b9b9b5"/>
          <stop offset="0.12" stop-color="#e9dcb8"/>
          <stop offset="0.45" stop-color="#f2b347"/>
          <stop offset="0.65" stop-color="#d8c9a0"/>
          <stop offset="0.72" stop-color="#1f1f1f"/>
          <stop offset="1" stop-color="#141414"/>
        </linearGradient>
        <linearGradient id="paper-b" x1="0" y1="0" x2="1" y2="1">
          <stop offset="0" stop-color="#ffffff"/>
          <stop offset="0.6" stop-color="#f1f1f1"/>
          <stop offset="1" stop-color="#ffffff"/>
        </linearGradient>
      </defs>

      <rect class="patio-photo" x="0" y="0" width="612" height="340" fill="url(#patio-b)" role="img" aria-label="Photo of outdoor patio seating on a terrace with greenery"/>
      <path class="orange-wave" d="M0,250 C200,256 430,222 612,118 L612,795 L0,795 Z" fill="var(--orange)"/>
      <path class="paper-wave" d="M0,413 C210,405 440,330 612,232 L612,795 L0,795 Z" fill="url(#paper-b)"/>

      <text class="title" x="32" y="78">SPIRAL FLAME</text>
      <text class="title" x="32" y="128">PROPANE</text>
      <text class="title title--accent" x="32" y="178">HEATER</text>
      <line x1="322" y1="42" x2="322" y2="195" stroke="#ffffff" stroke-opacity="0.55" stroke-width="1"/>

      <g class="perks">
        <circle cx="340" cy="64" r="6.5" fill="var(--orange)"/><path d="M337,64 l2.2,2.2 l4,-4.4" stroke="#fff" stroke-width="1.6" fill="none"/>
        <text class="perk" x="355" y="68">AVAILABLE TO PURCHASE</text>
        <circle cx="340" cy="93" r="6.5" fill="var(--orange)"/><path d="M337,93 l2.2,2.2 l4,-4.4" stroke="#fff" stroke-width="1.6" fill="none"/>
        <text class="perk" x="355" y="97">AVAILABLE TO RENT</text>
        <circle cx="340" cy="122" r="6.5" fill="var(--orange)"/><path d="M337,122 l2.2,2.2 l4,-4.4" stroke="#fff" stroke-width="1.6" fill="none"/>
        <text class="perk" x="355" y="126">SEASONAL RENTAL PROGRAMS</text>
        <text class="perk" x="355" y="140">FOR RESTAURANT AND HOSPITALITY</text>
        <text class="perk" x="355" y="155">COMPANIES</text>
      </g>

      <text class="section-head" x="33" y="292">SPECIFICATIONS</text>
      <g class="specs">
        <circle class="spec-dot" cx="37" cy="312" r="2"/><text class="spec" x="48" y="316">ADJUSTABLE HEAT CONTROL TO  48,000 BTU</text>
        <circle class="spec-dot" cx="37" cy="331" r="2"/><text class="spec" x="48" y="335">BLACK POWDER COATED FINISH</text>
        <circle class="spec-dot" cx="37" cy="349" r="2"/><text class="spec" x="48" y="353">USES 20 LBS. PROPANE TANK</text>
        <circle class="spec-dot" cx="37" cy="368" r="2"/><text class="spec" x="48" y="372">CE, GS, AGA, CSA, WITH ETL CERTIFICATE</text>
        <text class="spec" x="48" y="391">AND ROHS APPROVED</text>
      </g>

      <rect class="product-photo" x="440" y="240" width="110" height="408" rx="32" fill="url(#product-b)" role="img" aria-label="Product photo of the spiral flame heater with fire rising up the middle of its glass tube"/>

      <text class="section-head" x="36" y="448">ADDITIONAL DETAILS</text>
      <g class="details">
        <circle class="bullet-dot" cx="37" cy="468" r="2"/><text class="detail" x="44" y="472">Commercial Quality</text>
        <circle class="bullet-dot" cx="37" cy="488" r="2"/><text class="detail" x="44" y="492">For Outdoor Use Only</text>
        <circle class="bullet-dot" cx="37" cy="508" r="2"/><text class="detail" x="44" y="512">Conforms to ANSI STD Z83.26-2014 Certified to CSA STD</text>
        <text class="detail" x="44" y="532">2.37-2014 Gas- fired outdoor infrared patio heaters</text>
        <circle class="bullet-dot" cx="37" cy="548" r="2"/><text class="detail" x="44" y="552">Safety Auto Shut Off Switch</text>
        <circle class="bullet-dot" cx="37" cy="568" r="2"/><text class="detail" x="44" y="572">Thermostatic Control</text>
        <circle class="bullet-dot" cx="37" cy="588" r="2"/><text class="detail" x="44" y="592">Piezoelectric Ignition</text>
        <circle class="bullet-dot" cx="37" cy="608" r="2"/><text class="detail" x="44" y="612">Base Diameter 17” - Anti-Tip Design</text>
        <circle class="bullet-dot" cx="37" cy="628" r="2"/><text class="detail" x="44" y="632">Standard Wheels - Tilt &amp; Move</text>
        <circle class="bullet-dot" cx="37" cy="648" r="2"/><text class="detail" x="44" y="652">Run time: 8-10 hours with standard 20 lbs. Propane tank</text>
        <circle class="bullet-dot" cx="37" cy="668" r="2"/><text class="detail" x="44" y="672">96” Tall</text>
        <circle class="bullet-dot" cx="37" cy="688" r="2"/><text class="detail" x="44" y="692">Heating Area: 200 sq. ft</text>
      </g>

      <g class="price-note">
        <circle cx="535" cy="580" r="70" fill="var(--orange-soft)" fill-opacity="0.95"/>
        <text class="note-head" x="531" y="552" text-anchor="middle">NOTE</text>
        <text class="note-price" x="535" y="576" text-anchor="middle">$450 each</text>
        <text class="note-small" x="535" y="593" text-anchor="middle">Assembly &amp; Delivery available</text>
        <text class="note-small" x="535" y="604" text-anchor="middle">upon request. Discounts</text>
        <text class="note-small" x="535" y="615" text-anchor="middle">for large quantity orders</text>
      </g>

      <path class="footer-stripe" d="M185,795 C255,690 370,662 612,650 L612,795 Z" fill="var(--orange)"/>
      <path class="footer-band" d="M215,795 C280,700 380,676 612,664 L612,795 Z" fill="var(--ink)"/>

      <g class="contact">
        <text class="contact-head" x="597" y="706" text-anchor="end">FOR INQUIRIES AND ORDERS:</text>
        <text class="contact-name" x="597" y="723" text-anchor="end">Contact:  Dana Reyes</text>
        <text class="contact-line" x="573" y="744" text-anchor="end">555-014-2271</text>
        <text class="contact-line" x="573" y="762" text-anchor="end">dana@tmarlowco.example</text>
        <text class="contact-line" x="573" y="780" text-anchor="end">42 - 48 Harbor Lane Millbrook, NJ 07000</text>
        <circle cx="590" cy="740" r="6" fill="var(--orange)"/>
        <path d="M587.5,737.5 q0,4 5,5" stroke="#fff" stroke-width="1.5" fill="none"/>
        <circle cx="590" cy="758" r="6" fill="var(--orange)"/>
        <circle cx="590" cy="758" r="3" stroke="#fff" stroke-width="1.1" fill="none"/>
        <circle cx="590" cy="776" r="6" fill="var(--orange)"/>
        <path d="M590,779.5 l-2.6,-3.4 a2.8,2.8 0 1 1 5.2,0 Z" fill="#fff"/>
      </g>

      <g class="brand">
        <text class="brand-name" x="48" y="760">TMC</text>
        <text class="brand-tagline" x="36" y="775">t. Marlow and company</text>
      </g>
    </svg>
  </section>

</main>
</body>
</html>
```